Eye Catching Business Card for Optometrist

We've recently refreshed our logo and now we need a fresh and bold look for our business cards. We provide progressive ways to improve people's vision and protect their eye health.

Use our new logo as guidance into the colors to use. As far as style goes, I love how bold and eye catching the card is for Lanternfield Studio. Feel free to use your creative judgement.

Tagline: "Caring sight for every generation."

pertinent info to include:

Dr. Marcus Velbrin
Optometrist

7258 Dunmore Ridge Blvd #215
Brantwell, MO 64172
(555) 382-9017

marc@brantwellfamilyeyecare.example
www.brantwellfamilyeyecare.example

```html
<!DOCTYPE html>
<html lang="en">
<head>
<meta charset="utf-8">
<title>Brantwell Family Eye Care – Business Card</title>
<link rel="stylesheet" href="https://fonts.googleapis.com/css2?family=Open+Sans:wght@400;600;700&family=Arimo:wght@400;700&display=swap">
<style>
  :root {
    --brand-red: #a3162a;
    --brand-brown: #54463a;
    --tagline-grey: #7a7a7a;
    --card-edge: #6b6b6b;
    --canvas-edge: #8a8a8a;
    --white: #ffffff;
  }
  * { margin: 0; padding: 0; box-sizing: border-box; }
  html, body { width: 1200px; height: 1000px; overflow: hidden; background: var(--white); }
  .canvas {
    position: relative; width: 1200px; height: 1000px;
    border: 1px solid var(--canvas-edge); background: var(--white); overflow: hidden;
  }
  .accent-bar { position: absolute; background: var(--brand-red); }
  .accent-bar--top { left: 1169px; top: 0; width: 31px; height: 185px; }
  .accent-bar--bottom { left: 0; top: 818px; width: 32px; height: 182px; }

  .card {
    position: absolute; left: 297px; width: 609px; height: 371px;
    border: 1px solid var(--card-edge); overflow: hidden;
    background: radial-gradient(ellipse at 70% 40%, #f1f1f1 0%, #fafafa 45%, #ffffff 80%);
  }
  .card--front { top: 143px; }
  .card--back { top: 569px; background: radial-gradient(ellipse at 45% 45%, #eeeeee 0%, #f7f7f7 45%, #ffffff 85%); }

  .business-name {
    position: absolute; font-family: "Open Sans", sans-serif; font-weight: 600;
    color: var(--brand-brown); line-height: 1; white-space: nowrap;
  }
  .card--front .business-name { left: 40px; top: 42px; font-size: 24px; }
  .tagline { position: absolute; font-family: "Open Sans", sans-serif; font-weight: 400; color: var(--tagline-grey); white-space: nowrap; }
  .card--front .tagline { left: 40px; top: 80px; font-size: 18px; }

  .band { position: absolute; left: 0; width: 100%; height: 25px; background: var(--brand-red); }
  .band--1 { top: 199px; } .band--2 { top: 230px; } .band--3 { top: 261px; }

  .mark-frame {
    position: absolute; left: 38px; top: 154px; width: 152px; height: 151px;
    border: 8px solid var(--brand-red); background: var(--white);
  }

  .doctor { position: absolute; left: 192px; top: 156px; font-family: "Open Sans", sans-serif; }
  .doctor__name { font-size: 20px; font-weight: 700; color: var(--brand-brown); letter-spacing: 0.5px; line-height: 1; }
  .doctor__role { font-family: "Arimo", sans-serif; font-size: 12.5px; color: var(--brand-red); margin-top: 4px; }

  .contact { position: absolute; left: 207px; display: flex; align-items: center; height: 25px;
    font-family: "Arimo", sans-serif; font-size: 15px; color: var(--white); white-space: nowrap; }
  .contact svg { width: 14px; height: 14px; margin-right: 19px; flex: none; }
  .contact--phone { top: 199px; } .contact--email { top: 230px; } .contact--web { top: 261px; }

  .address-bar { position: absolute; left: 0; top: 325px; width: 100%; height: 46px; background: var(--brand-brown);
    display: flex; align-items: center; padding-left: 61px;
    font-family: "Arimo", sans-serif; font-size: 18px; color: var(--white); white-space: nowrap; }
  .address-bar svg { width: 16px; height: 20px; margin-right: 19px; flex: none; }

  .brand-square { position: absolute; left: 254px; top: 60px; width: 100px; height: 100px; background: var(--brand-red); }
  .card--back .business-name { left: 0; width: 100%; top: 200px; text-align: center; font-size: 34px; }
  .card--back .tagline { left: 0; width: 100%; top: 291px; text-align: center; font-size: 26px; }
</style>
</head>
<body>
<div class="canvas">
  <div class="accent-bar accent-bar--top"></div>
  <div class="accent-bar accent-bar--bottom"></div>

  <section class="card card--front">
    <p class="business-name">Brantwell Family Eye Care</p>
    <p class="tagline">Caring sight for every generation</p>

    <div class="band band--1"></div>
    <div class="band band--2"></div>
    <div class="band band--3"></div>
    <div class="mark-frame"></div>

    <div class="doctor">
      <p class="doctor__name">DR. MARCUS VELBRIN</p>
      <p class="doctor__role">Optometrist</p>
    </div>

    <div class="contact contact--phone">
      <svg viewBox="0 0 24 24" aria-hidden="true"><path fill="#fff" d="M6.6 10.8a15.1 15.1 0 0 0 6.6 6.6l2.2-2.2c.3-.3.7-.4 1-.2 1.1.4 2.3.6 3.6.6.6 0 1 .4 1 1V20c0 .6-.4 1-1 1A17 17 0 0 1 3 4c0-.6.4-1 1-1h3.5c.6 0 1 .4 1 1 0 1.3.2 2.5.6 3.6.1.3 0 .7-.2 1z"/></svg>
      <span>(555) 382-9017</span>
    </div>
    <div class="contact contact--email">
      <svg viewBox="0 0 24 24" aria-hidden="true"><rect x="2.5" y="5" width="19" height="14" fill="none" stroke="#fff" stroke-width="1.8"/><path d="M2.5 5l9.5 8 9.5-8M2.5 19l7-6.5M21.5 19l-7-6.5" fill="none" stroke="#fff" stroke-width="1.6"/></svg>
      <span>marc@brantwellfamilyeyecare.example</span>
    </div>
    <div class="contact contact--web">
      <svg viewBox="0 0 24 24" aria-hidden="true"><g fill="none" stroke="#fff" stroke-width="1.6"><circle cx="12" cy="12" r="9.5"/><ellipse cx="12" cy="12" rx="4.2" ry="9.5"/><path d="M2.5 12h19M4 7h16M4 17h16"/></g></svg>
      <span>www.brantwellfamilyeyecare.example</span>
    </div>

    <div class="address-bar">
      <svg viewBox="0 0 16 20" aria-hidden="true"><path fill="#fff" d="M8 0a7 7 0 0 0-7 7c0 5 7 13 7 13s7-8 7-13a7 7 0 0 0-7-7zm0 10a3 3 0 1 1 0-6 3 3 0 0 1 0 6z"/></svg>
      <span>7258 Dunmore Ridge Blvd #215 Brantwell, MO 64172</span>
    </div>
  </section>

  <section class="card card--back">
    <div class="brand-square"></div>
    <p class="business-name">Brantwell Family Eye Care</p>
    <p class="tagline">Caring sight for every generation</p>
  </section>
</div>
</body>
</html>
```